Stylish business cards for KV7

To create an appealing and professional business card design for a WOMEN Owned Construction Supply Company.
2 sided card. Incorporate brand elements, curvy, colorful, sleek and bright. No solid white background. attached samples of styles added shapes/ribbons. Want something with that WOW that looks awesome, factor. It is a new logo, so feel free to mess with logo colors in the blue and teal factors that can look good with both dark and light background. If you want to try a watermark with just the KV7, without the "Supply" that might look cool to.

Industry/Entity Type

Women owned construction supply company

Contact Information for Business Card

Name, Title, and phone number and email, web page. maybe spot for qr code.

Font styles to use
Sans Serif

Requirements
Nice to have
• would love to see colors, maybe stylish ribbon dividers or some sort of 2 or 3 tone color card that compliments logo.
Should not have
• Please do not have all white background. Do not include Home/reale state/ or building images.

```html
<!DOCTYPE html>
<html lang="en">
<head>
<meta charset="utf-8">
<title>KV7 Supply – Business Cards</title>
<link rel="stylesheet" href="https://fonts.googleapis.com/css2?family=Montserrat:wght@400;500;700&display=swap">
<style>
  :root {
    --navy: #1b3a5c;
    --navy-deep: #15304d;
    --navy-text: #1d3656;
    --teal: #2594b9;
    --teal-soft: #bcdbe6;
    --card-light: #f4f4f4;
    --card-tint: #e3e9ee;
    --backdrop: #1e1e1e;
  }
  * { box-sizing: border-box; margin: 0; padding: 0; }
  html, body {
    width: 1200px; height: 1059px; overflow: hidden;
    background: var(--backdrop);
    font-family: "Montserrat", sans-serif;
  }
  .canvas { position: relative; width: 1200px; height: 1059px; }

  .card {
    position: absolute;
    width: 688px; height: 391px;
    border-radius: 18px;
    overflow: hidden;
  }
  .card--front {
    left: 256px; top: 89px;
    background: linear-gradient(120deg, var(--card-light) 0%, var(--card-light) 45%, var(--card-tint) 100%);
    color: var(--navy-text);
  }
  .card--back {
    left: 254px; top: 547px;
    background: linear-gradient(150deg, var(--navy) 0%, var(--navy-deep) 100%);
  }

  .ribbons { position: absolute; inset: 0; width: 100%; height: 100%; }

  .brand { position: absolute; font-weight: 700; letter-spacing: 0.5px; white-space: nowrap; }
  .card--front .brand { left: 37px; top: 92px; font-size: 40px; color: var(--navy); }
  .card--back .brand { left: 0; right: 0; top: 150px; text-align: center; font-size: 64px; color: #ffffff; }

  .address { position: absolute; left: 37px; top: 224px; font-size: 15px; line-height: 20px; }
  .contacts { position: absolute; left: 37px; top: 280px; list-style: none; font-size: 15px; }
  .contacts li { display: flex; align-items: center; height: 25px; }
  .contacts svg { width: 13px; height: 13px; margin-right: 7px; fill: var(--teal); }

  .person { position: absolute; right: 31px; top: 170px; text-align: right; }
  .person__name { font-size: 23px; font-weight: 700; color: var(--navy-text); letter-spacing: 0.3px; line-height: 28px; }
  .person__title { font-size: 14px; font-weight: 400; color: var(--teal); margin-top: 2px; }
  .accent-bar { position: absolute; right: 0; top: 177px; width: 16px; height: 38px; background: var(--teal); }
</style>
</head>
<body>
<main class="canvas">
  <section class="card card--front" aria-label="Card front">
    <svg class="ribbons" viewBox="0 0 688 391" preserveAspectRatio="none" aria-hidden="true">
      <path d="M330 391 C420 330 520 300 688 290 L688 391 Z" fill="var(--teal-soft)" opacity="0.55"/>
      <path d="M420 391 C500 350 590 330 688 326 L688 391 Z" fill="var(--teal)" opacity="0.85"/>
      <path d="M520 391 C580 368 640 358 688 356 L688 391 Z" fill="var(--navy)"/>
      <path d="M300 325 C420 300 540 296 688 300" fill="none" stroke="var(--teal)" stroke-width="2" opacity="0.5"/>
    </svg>
    <div class="brand">KV7 Supply</div>
    <p class="address">P.O Box 4120 Harbour Road<br>Westbridge QLD 4000</p>
    <ul class="contacts">
      <li><svg viewBox="0 0 24 24" aria-hidden="true"><path d="M6.6 10.8a15.1 15.1 0 0 0 6.6 6.6l2.2-2.2a1 1 0 0 1 1-.25 11.4 11.4 0 0 0 3.6.57 1 1 0 0 1 1 1V20a1 1 0 0 1-1 1A17 17 0 0 1 3 4a1 1 0 0 1 1-1h3.5a1 1 0 0 1 1 1c0 1.25.2 2.450.57 3.57a1 1 0 0 1-.25 1z"/></svg>555.014.2278</li>
      <li><svg viewBox="0 0 24 24" aria-hidden="true"><path d="M2 5h20v14H2zM3.5 6.5v.4l8.5 6 8.5-6v-.4zM3.5 8.8v8.7h17V8.8L12 14.8z"/></svg>info@kv7supply.com.au</li>
      <li><svg viewBox="0 0 24 24" aria-hidden="true"><path d="M12 2a10 10 0 1 0 0 20 10 10 0 0 0 0-20zm6.9 6h-3a15.6 15.6 0 0 0-1.4-3.6A8 8 0 0 1 18.9 8zM12 4a14 14 0 0 1 1.9 4h-3.8A14 14 0 0 1 12 4zM4.3 14a8 8 0 0 1 0-4h3.4a16 16 0 0 0 0 4zm.8 2h3a15.6 15.6 0 0 0 1.4 3.6A8 8 0 0 1 5.1 16zm3-8h-3a8 8 0 0 1 4.4-3.6A15.6 15.6 0 0 0 8.1 8zM12 20a14 14 0 0 1-1.9-4h3.8A14 14 0 0 1 12 20zm2.3-6H9.7a14.7 14.7 0 0 1 0-4h4.6a14.7 14.7 0 0 1 0 4zm.2 5.6a15.6 15.6 0 0 0 1.4-3.6h3a8 8 0 0 1-4.4 3.6zm1.8-5.6a16 16 0 0 0 0-4h3.4a8 8 0 0 1 0 4z"/></svg>www.kv7supply.com.au</li>
    </ul>
    <div class="person">
      <div class="person__name">DANA WELLS</div>
      <div class="person__title">CEO/Founder</div>
    </div>
    <div class="accent-bar"></div>
  </section>

  <section class="card card--back" aria-label="Card back">
    <svg class="ribbons" viewBox="0 0 688 391" preserveAspectRatio="none" aria-hidden="true">
      <path d="M0 391 C150 330 360 310 688 330 L688 391 Z" fill="var(--teal)" opacity="0.12"/>
      <path d="M280 340 C420 318 560 316 688 324" fill="none" stroke="var(--teal)" stroke-width="6" stroke-linecap="round" opacity="0.3"/>
      <path d="M220 258 C330 244 460 240 600 246" fill="none" stroke="var(--teal)" stroke-width="5" stroke-linecap="round"/>
    </svg>
    <div class="brand">KV7 Supply</div>
  </section>
</main>
</body>
</html>
```